wealth management firm, professional group, new model

we have a logo that works but we need a card, white background using our colors...clean look

our tag line if can be used in

The Path From Saver to Steward

```html
<!DOCTYPE html>
<html lang="en">
<head>
<meta charset="utf-8">
<title>Varro Wealth Partners – Business Card</title>
<link rel="stylesheet" href="https://fonts.googleapis.com/css2?family=Montserrat:wght@400;500;700&display=swap">
<style>
  :root {
    --navy: #1b2d52;
    --white: #ffffff;
    --backdrop: #e9e9eb;
    --ink-soft: rgba(255,255,255,0.92);
  }
  * { box-sizing: border-box; margin: 0; padding: 0; }
  html, body {
    width: 1200px; height: 896px; overflow: hidden;
    background: var(--backdrop);
    font-family: "Montserrat", sans-serif;
  }
  .canvas {
    width: 1200px; height: 896px;
    display: flex; align-items: center; justify-content: center; gap: 50px;
  }
  .card {
    width: 525px; height: 300px; border-radius: 18px; overflow: hidden;
    position: relative;
    box-shadow: 0 8px 24px rgba(20,30,50,0.14);
  }
  /* Front */
  .card-front { background: var(--white); color: var(--navy); }
  .front-brand {
    position: absolute; top: 0; left: 0; right: 0; bottom: 44px;
    display: flex; flex-direction: column; align-items: center; justify-content: center;
  }
  .brand-row { display: flex; align-items: center; gap: 22px; }
  .brand-dot { width: 18px; height: 18px; border-radius: 50%; background: var(--navy); }
  .brand-name {
    font-size: 50px; font-weight: 500; letter-spacing: 0.42em;
    margin-right: -0.42em; line-height: 1;
  }
  .brand-sub {
    margin-top: 26px; font-size: 17px; font-weight: 500; letter-spacing: 0.16em;
  }
  .tagline-band {
    position: absolute; left: 0; right: 0; bottom: 0; height: 44px;
    background: var(--navy); color: var(--white);
    display: flex; align-items: center; justify-content: center;
    font-size: 13px; font-weight: 500; letter-spacing: 0.2em; text-transform: uppercase;
  }
  /* Back */
  .card-back {
    background: var(--navy); color: var(--white);
    display: flex; flex-direction: column; align-items: center; text-align: center;
    padding-top: 52px;
  }
  .person-name { font-size: 29px; font-weight: 700; letter-spacing: 0.14em; line-height: 1; }
  .person-title { margin-top: 12px; font-size: 16px; font-weight: 400; letter-spacing: 0.03em; }
  .back-mark {
    margin-top: 38px; font-size: 26px; font-weight: 500; letter-spacing: 0.42em;
    margin-right: -0.42em;
  }
  .contact { margin-top: 44px; font-size: 13.5px; line-height: 1.6; color: var(--ink-soft); }
  .contact .sep { margin: 0 8px; }
</style>
</head>
<body>
<main class="canvas">
  <section class="card card-front" aria-label="Card front">
    <div class="front-brand">
      <div class="brand-row">
        <span class="brand-dot"></span>
        <span class="brand-name">VARRO</span>
      </div>
      <div class="brand-sub">WEALTH PARTNERS</div>
    </div>
    <div class="tagline-band">The Path From Saver to Steward</div>
  </section>

  <section class="card card-back" aria-label="Card back">
    <h1 class="person-name">JORDAN HALE</h1>
    <p class="person-title">Senior Wealth Advisor</p>
    <p class="back-mark">VARRO</p>
    <p class="contact">
      jordan@varrowealth.com<span class="sep">|</span>+1(555) 410-2297<br>
      varrowealth.com
    </p>
  </section>
</main>
</body>
</html>
```